Modern Business Card

Modern professional business card with more than just logo and demographic info. Something memorable.

We are a trendy/modern chiropractic group with an emphasis on neurology, hence the minimalist-type brain logo. We want to convey that modern and technical aspect with professionalism and the elite nature of our practice environment.

```html
<!DOCTYPE html>
<html lang="en">
<head>
<meta charset="utf-8">
<title>Northway Chiropractic – Business Card</title>
<link rel="stylesheet" href="https://fonts.googleapis.com/css2?family=Open+Sans:ital,wght@0,400;0,600;0,700;1,400&display=swap">
<style>
  :root {
    --brand-blue: #4680c2;
    --ink: #1e1e1e;
    --text-grey: #555a60;
    --stripe-grey: #55585c;
    --paper: #ffffff;
    --backdrop: #2a2b2d;
  }
  * { margin: 0; padding: 0; box-sizing: border-box; }
  html, body {
    width: 1200px; height: 900px; overflow: hidden;
    background: var(--backdrop);
    font-family: "Open Sans", Arial, sans-serif;
  }
  .stage {
    position: relative; width: 1200px; height: 900px;
    display: flex; flex-direction: column; align-items: center;
    justify-content: center; gap: 24px;
  }
  .card {
    position: relative; width: 700px; height: 400px; overflow: hidden;
    box-shadow: 0 10px 30px rgba(0,0,0,.45);
  }
  /* Front */
  .card-front { background: var(--paper); }
  .holder { position: absolute; left: 44px; top: 140px; }
  .holder-name {
    color: var(--brand-blue); font-weight: 700; font-size: 25px;
    letter-spacing: .5px; text-transform: uppercase; line-height: 1.1;
  }
  .holder-title { color: var(--text-grey); font-size: 16px; margin-top: 2px; }
  .divider {
    position: absolute; left: 44px; right: 56px; top: 218px;
    height: 1px; background: var(--brand-blue);
  }
  .contact { position: absolute; left: 44px; top: 236px; list-style: none; }
  .contact li {
    display: flex; align-items: center; gap: 8px;
    color: var(--text-grey); font-size: 16px; line-height: 28px;
  }
  .contact svg { width: 14px; height: 14px; fill: var(--brand-blue); }
  .brand {
    position: absolute; right: 60px; top: 96px;
    display: flex; align-items: center; gap: 14px;
  }
  .brand-dot { width: 46px; height: 46px; border-radius: 50%; background: var(--brand-blue); }
  .brand-name {
    color: var(--ink); font-weight: 600; text-transform: uppercase;
    line-height: 1; letter-spacing: 1px;
  }
  .brand-name .line-1 { display: block; font-size: 40px; }
  .brand-name .line-2 { display: block; font-size: 22px; letter-spacing: 2.4px; margin-top: 4px; }
  .address {
    position: absolute; right: 56px; top: 236px; text-align: right;
    color: var(--text-grey); font-size: 16px; line-height: 26px;
  }
  .footer-band { position: absolute; left: 0; bottom: 0; width: 700px; height: 110px; }
  .website {
    position: absolute; right: 56px; bottom: 7px;
    color: var(--paper); font-size: 16px;
  }
  /* Back */
  .card-back {
    background: var(--brand-blue);
    display: flex; align-items: center; justify-content: center;
  }
  .card-back .brand { position: static; }
  .card-back .brand-dot { background: var(--paper); width: 60px; height: 60px; }
  .card-back .brand-name { color: var(--paper); }
  .card-back .brand-name .line-1 { font-size: 54px; }
  .card-back .brand-name .line-2 { font-size: 30px; letter-spacing: 3.4px; }
</style>
</head>
<body>
<main class="stage">
  <section class="card card-front" aria-label="Business card front">
    <div class="holder">
      <p class="holder-name">Daniel Reyes</p>
      <p class="holder-title">President</p>
    </div>
    <div class="divider"></div>
    <ul class="contact">
      <li>
        <svg viewBox="0 0 24 24" aria-hidden="true"><path d="M6.6 10.8a15.1 15.1 0 0 0 6.6 6.6l2.2-2.2a1 1 0 0 1 1-.25 11.4 11.4 0 0 0 3.6.57 1 1 0 0 1 1 1V20a1 1 0 0 1-1 1A17 17 0 0 1 3 4a1 1 0 0 1 1-1h3.5a1 1 0 0 1 1 1c0 1.25.2 2.45.57 3.57a1 1 0 0 1-.25 1z"/></svg>
        555-014-2290
      </li>
      <li>
        <svg viewBox="0 0 24 24" aria-hidden="true"><path d="M2 5h20v14H2z M2 5l10 8 10-8" /></svg>
        daniel@northwaychiro.com
      </li>
    </ul>
    <div class="brand">
      <span class="brand-dot"></span>
      <p class="brand-name"><span class="line-1">Northway</span><span class="line-2">Chiropractic</span></p>
    </div>
    <address class="address" style="font-style:normal">
      1820 Harbor Crest Way<br>Bayview CA 90412
    </address>
    <svg class="footer-band" viewBox="0 0 700 110" aria-hidden="true">
      <path d="M0 18 L355 88 Q372 92 380 98 L0 98 Z" fill="var(--stripe-grey)"/>
      <path d="M0 30 L340 92 Q360 82 390 82 L700 82 L700 110 L0 110 Z" fill="var(--brand-blue)"/>
      <path d="M0 24 L350 90" stroke="var(--paper)" stroke-width="5" fill="none"/>
    </svg>
    <p class="website">northwaychiro.com</p>
  </section>

  <section class="card card-back" aria-label="Business card back">
    <div class="brand">
      <span class="brand-dot"></span>
      <p class="brand-name"><span class="line-1">Northway</span><span class="line-2">Chiropractic</span></p>
    </div>
  </section>
</main>
</body>
</html>
```